The Velvet Rig

need a business card for a dj and sound equipment hire(rentals) business based in Melbourne. i have attached a current card get an idea. card needs to be unique professional looking.

ps.this card is not for a DJ. it's a rental business of dj equipment and pa systems.

Industry/Entity Type

Business

Font styles to use
Sans Serif
Script

Requirements
Must have
• Business Name: THE VELVET RIG
Contact Person: KIERAN MALLORY
Mobile: 047 VELVET 91
Email: KIERAN@THEVELVETRIG.COM.AU
Website: WWW.THEVELVETRIG.COM.AU
Pixelwall: WWW.PIXELWALL.CM/THEVELVETRIG.COM.AU

```html
<!DOCTYPE html>
<html lang="en">
<head>
<meta charset="utf-8">
<title>The Velvet Rig – Business Card</title>
<link href="https://fonts.googleapis.com/css2?family=Arimo:wght@400;700&family=Kristi&display=swap" rel="stylesheet">
<style>
  :root {
    --page: #ffffff;
    --card: #ffffff;
    --ink: #4d4d4f;
    --blue: #1aa0dc;
    --eq-top: #9fd9f5;
    --eq-bottom: #0f9bdc;
  }
  html, body {
    margin: 0;
    width: 1200px;
    height: 848px;
    overflow: hidden;
    background: var(--page);
    font-family: "Arimo", Arial, sans-serif;
  }
  .card {
    position: absolute;
    left: 322px;
    top: 265px;
    width: 556px;
    height: 336px;
    background: var(--card);
    border-radius: 12px;
    overflow: hidden;
    box-shadow: 0 3px 8px rgba(0,0,0,0.22);
  }
  .brand {
    position: absolute;
    left: 30px;
    top: 24px;
    width: 100px;
    text-align: center;
  }
  .brand-mark {
    display: block;
    width: 60px;
    height: 60px;
    margin: 0 auto;
    border-radius: 50%;
    background: var(--blue);
  }
  .brand-name {
    display: block;
    margin-top: 6px;
    font-family: "Kristi", cursive;
    font-size: 21px;
    line-height: 24px;
    font-weight: 400;
    color: var(--ink);
    white-space: nowrap;
  }
  .contact {
    position: absolute;
    right: 48px;
    top: 123px;
    text-align: right;
  }
  .contact-name {
    margin: 0 0 7px;
    font-size: 22px;
    font-weight: 700;
    letter-spacing: 0.6px;
    color: var(--ink);
  }
  .contact-line {
    margin: 0;
    font-size: 10.5px;
    line-height: 14.6px;
    color: var(--blue);
  }
  .contact-line .plus,
  .contact-line .word { color: var(--ink); }
  .contact-line .plus { font-weight: 700; }
  .contact-line.web { font-weight: 700; }
  .equalizer-band {
    position: absolute;
    left: 16px;
    top: 247px;
    width: 526px;
    height: 89px;
    background: linear-gradient(to bottom, var(--eq-top), var(--eq-bottom) 45%);
  }
</style>
</head>
<body>
  <div class="card">
    <div class="brand">
      <span class="brand-mark"></span>
      <span class="brand-name">The Velvet Rig</span>
    </div>

    <div class="contact">
      <p class="contact-name">KIERAN MALLORY</p>
      <p class="contact-line"><span class="plus">+</span> 047 <span class="word">VELVET</span> 91</p>
      <p class="contact-line">kieran@thevelvetrig.com.au</p>
      <p class="contact-line">www.pixelwall.cm/thevelvetrig.com.au</p>
      <p class="contact-line web">www.thevelvetrig.com.au</p>
    </div>

    <div class="equalizer-band" role="img" aria-label="Blue audio equalizer level bars pattern along the bottom edge"></div>
  </div>
</body>
</html>
```